KR Appraisals website redesign

I would like to refresh my existing website of www.krappraisals-example.com with new graphics, look and feel, as well as updated structure and wording. Content and layout changes have been uploaded to this project Brief.

My existing website has a dark feel. I am now looking for a light and energetic feel. Financial Services is my industry, so the website should be reflect that. I would also like to reflect the concepts of Trust, Service and Expertise.

The website must be serious and upmarket.

Target Market(s)

Corporate board members, CFO's, treasurers and controllers
Auditors, tax advisors, private equity and venture capital asset managers, investors, tax authorities

Industry/Entity Type

Financial Service

Coding

Coded - Design and coding required

Number of Pages Required

5+ page

Font styles to use
Sans Serif
Other font styles liked:
• Designer can choose another modern font

Colors
0355a3
3277b5
85acd3
eaf1f7
f37122
f68d4d
9bcb3c
acd037
cadf82

Requirements
Must have
• Good hi resolution pictures that convey "Finance", "Trust", "Service" or "Expertise".
• An anti-bot (such as Captcha) mechanism in the contact form.
Should not have
• Must not have all content on one rolling screen.

```html
<!DOCTYPE html>
<html lang="en">
<head>
<meta charset="utf-8">
<title>KR Appraisals — Business &amp; Intellectual Property Valuations</title>
<link href="https://fonts.googleapis.com/css2?family=Mulish:wght@300;400;600;700&display=swap" rel="stylesheet">
<style>
:root{
  --blue-deep:#0355a3;
  --blue:#3277b5;
  --blue-soft:#85acd3;
  --blue-mist:#eaf1f7;
  --orange:#f37122;
  --orange-soft:#f68d4d;
  --green:#9bcb3c;
  --green-soft:#cadf82;
  --ink:#1f3550;
  --text:#4e5a66;
  --paper:#ffffff;
}
*{box-sizing:border-box;margin:0;padding:0}
html,body{width:1200px;height:3924px;overflow:hidden;background:var(--paper)}
body{position:relative;font-family:"Mulish",sans-serif;color:var(--text)}
.abs{position:absolute}
.btn-outline{position:absolute;border:2px solid currentColor;display:flex;align-items:center;justify-content:center;font-size:15px;letter-spacing:.3px;text-transform:uppercase;font-weight:600}

/* hero */
.hero-photo{left:0;top:0;width:1200px;height:760px;background:linear-gradient(180deg,#3277b5 0%,#5b8fc4 20%,#f68d4d 34%,#85acd3 50%,#3277b5 72%,#0355a3 100%)}
.nav{top:46px;display:flex;gap:40px;font-size:17px;color:#fff;text-transform:uppercase}
.nav.left{left:123px}.nav.right{left:751px}
.nav .current{font-weight:700;position:relative}
.nav .current::after{content:"";position:absolute;left:4px;right:4px;bottom:-12px;height:2px;background:var(--green-soft);border-radius:2px}
.brand-box{left:493px;top:18px;width:203px;height:84px;border:2px solid #fff;display:flex;align-items:flex-end;justify-content:center;padding-bottom:8px;color:#fff;font-size:22px;text-transform:uppercase;white-space:nowrap}
.hero-title{left:0;width:1200px;top:272px;text-align:center;color:#fff;font-size:52px;font-weight:600;text-transform:uppercase;line-height:1}
.hero-sub{left:0;width:1200px;top:326px;text-align:center;color:#fff;font-size:40px;font-weight:400;text-transform:uppercase;line-height:1.1}
.hero .btn-outline{left:507px;top:393px;width:180px;height:47px;color:#fff;font-weight:400}
.arrow{top:300px;width:30px;height:54px}

/* trust */
.brand-big{left:104px;top:815px;width:440px;height:239px;display:flex;align-items:center;justify-content:center;font-size:54px;font-weight:700;color:var(--blue-deep);white-space:nowrap}
.trust h2{left:598px;top:812px;font-size:31px;font-weight:600;color:var(--ink)}
.trust p{left:598px;width:500px;font-size:16px;line-height:24px;color:var(--text)}
.trust .btn-outline{left:600px;top:1040px;width:175px;height:46px;color:var(--blue-deep)}

/* career */
.career-card{left:163px;top:1291px;width:556px;height:334px;background:#fff;box-shadow:0 2px 14px rgba(3,85,163,.14);padding:52px 60px}
.career-card h2{font-size:29px;font-weight:600;color:var(--ink);margin-bottom:14px}
.career-card p{font-size:15.5px;line-height:24px;margin-bottom:8px;color:var(--text)}
.career-card .btn-outline{left:60px;top:250px;width:156px;height:42px;font-size:13.5px;color:var(--blue-deep)}

/* section headers */
.sec-head{left:0;width:1200px;text-align:center}
.sec-head .mark{font-size:15px;font-weight:700;letter-spacing:2px;text-transform:uppercase}
.sec-head h2{font-size:32px;font-weight:600;text-transform:uppercase;margin-top:4px}

/* services */
.services-bg{left:0;top:1640px;width:1200px;height:880px;background:linear-gradient(180deg,var(--blue-mist),#f7fafd 50%,var(--blue-mist))}
.service{width:270px;height:291px;background:#fff;box-shadow:0 2px 10px rgba(3,85,163,.16);text-align:center;padding:34px 22px 0}
.service svg{width:68px;height:68px;stroke:var(--blue);fill:none;stroke-width:1.6}
.service h3{font-size:18px;font-weight:600;color:var(--ink);text-transform:uppercase;line-height:24px;margin:12px 0 14px}
.service p{font-size:12.5px;line-height:19px;color:var(--text)}
.service.active{background:var(--blue)}
.service.active h3,.service.active p{color:#fff}
.service.active svg{stroke:#fff}

/* news */
.news-band{left:0;top:2523px;width:1200px;height:721px;background:linear-gradient(180deg,var(--blue),var(--blue-soft) 55%,var(--blue))}
.news-card{width:275px;height:375px;background:#fff;box-shadow:0 2px 10px rgba(3,53,100,.25)}
.news-card .thumb{height:172px}
.news-card .body{padding:22px 14px 0 16px}
.news-card h3{font-size:14px;font-weight:600;color:var(--ink);line-height:22px;margin-bottom:12px}
.news-card .date{font-size:12.5px;color:var(--text);display:flex;align-items:center;gap:8px;margin-bottom:10px}
.news-card .date svg rect,.news-card .date svg path{stroke:var(--green)}
.news-card p{font-size:12px;line-height:19px;color:var(--text)}

/* contact */
.contact-bg{left:0;top:3244px;width:1200px;height:467px;background:var(--blue-mist)}
.field{background:#fff;border:2px solid var(--blue-soft);font-size:15px;color:#6b7885;padding:0 22px;display:flex;align-items:center}
.field.area{align-items:flex-start;padding-top:14px}
.captcha{left:142px;top:3577px;width:250px;height:50px;background:#fff;border:2px solid var(--blue-soft);display:flex;align-items:center;gap:12px;padding:0 14px;font-size:14px;color:var(--text)}
.captcha .box{width:22px;height:22px;border:2px solid var(--green);border-radius:3px}
.submit{left:504px;top:3575px;width:187px;height:54px;background:var(--orange);color:#fff;font-size:20px;font-weight:600;display:flex;align-items:center;justify-content:center;text-transform:uppercase}

/* footer */
.footer-brand{left:0;width:1200px;top:3735px;text-align:center;font-size:26px;font-weight:600;color:var(--blue-deep)}
.footer-nav{left:0;width:1200px;top:3794px;display:flex;justify-content:center;gap:44px;font-size:18px;color:var(--ink);text-transform:uppercase}
.copy{left:0;width:1200px;top:3826px;text-align:center;font-size:13.5px;color:var(--text)}
.socials{left:0;width:1200px;top:3867px;display:flex;justify-content:center;gap:9px}
.socials span{width:35px;height:35px;border:2px solid var(--blue);border-radius:50%}
</style>
</head>
<body>

<section class="hero">
  <div class="abs hero-photo" role="img" aria-label="City skyline with highway light trails at dusk"></div>
  <svg class="abs" style="left:0;top:500px" width="1200" height="260" viewBox="0 500 1200 260">
    <path d="M0 586 L366 746 L1200 518 L1200 760 L0 760 Z" fill="#fff"/>
    <path d="M0 586 L340 735 Q366 748 392 739 L1200 518" fill="none" stroke="#3277b5" stroke-width="5"/>
    <path d="M0 604 L340 752 Q366 762 392 754 L1200 534" fill="none" stroke="#85acd3" stroke-width="1.5"/>
  </svg>
  <nav class="abs nav left"><span class="current">Home</span><span>Services</span><span>News &amp; Views</span></nav>
  <div class="abs brand-box">KR Appraisals</div>
  <nav class="abs nav right"><span>About</span><span>Career</span><span>Contact Us</span></nav>
  <svg class="abs arrow" style="left:104px" viewBox="0 0 30 54"><path d="M26 2 L4 27 L26 52" fill="none" stroke="#fff" stroke-width="2"/></svg>
  <svg class="abs arrow" style="left:1068px" viewBox="0 0 30 54"><path d="M4 2 L26 27 L4 52" fill="none" stroke="#fff" stroke-width="2"/></svg>
  <h1 class="abs hero-title">Business &amp; Intellectual</h1>
  <div class="abs hero-sub">Property Valuations</div>
  <div class="btn-outline">Learn More</div>
</section>

<section class="trust">
  <div class="abs brand-big">KR Appraisals</div>
  <h2 class="abs">TRUST, SERVICE &amp; EXPERTISE</h2>
  <p class="abs" style="top:871px">Trust is paramount. Clients rely on KR Appraisals Services for confidentiality, transparency and independence.</p>
  <p class="abs" style="top:942px">Service is front and center in KR Appraisals Services’ product offerings. KR Appraisals Services considers the needs of all stakeholders and the personal needs of the client team involved.</p>
  <div class="btn-outline">Learn More</div>
</section>

<section class="career">
  <svg class="abs" style="left:0;top:1120px" width="1200" height="590" viewBox="0 1120 1200 590">
    <defs>
      <linearGradient id="careerLight" x1="0" y1="0" x2="1" y2="0"><stop offset="0" stop-color="#eaf1f7"/><stop offset="1" stop-color="#cfe0ef"/></linearGradient>
      <linearGradient id="careerPhoto" x1="0" y1="0" x2="1" y2="1"><stop offset="0" stop-color="#aecbe6"/><stop offset=".5" stop-color="#3277b5"/><stop offset="1" stop-color="#85acd3"/></linearGradient>
    </defs>
    <path d="M180 1182 L740 1182 L740 1300 L180 1300 Z" fill="url(#careerLight)" role="img" aria-label="Office wall with financial charts"/>
    <path d="M180 1182 L330 1182 L260 1235 Z" fill="#fff"/>
    <path d="M180 1200 L340 1290" stroke="#3277b5" stroke-width="4"/>
    <path d="M719 1182 L1200 1182 L1200 1553 L1060 1676 Q1036 1694 1008 1680 L719 1538 Z" fill="url(#careerPhoto)" role="img" aria-label="Business advisor presenting to a client in an office"/>
    <path d="M719 1545 L1004 1690 Q1036 1706 1064 1686 L1200 1568" fill="none" stroke="#3277b5" stroke-width="5"/>
  </svg>
  <div class="abs career-card">
    <h2>OUR CAREER</h2>
    <p>Pellentesque faucibus Ut accumsan ultricies elit Maecenas at justo id velit placerat molestie Donec dictum</p>
    <p>Aectus non odio Cras a ante vitae enim iaculis aliquam Mauris nunc&nbsp; est nunc venenatis in tristique eu imperdiet ac nisl Cum sociis natoque penatibus et magnis dis parturient</p>
    <div class="btn-outline">Learn More</div>
  </div>
</section>

<section class="services">
  <div class="abs services-bg"></div>
  <div class="abs sec-head" style="top:1684px;color:var(--ink)"><div class="mark" style="color:var(--blue-deep)">KR Appraisals</div><h2>Our Services</h2></div>

  <div class="abs service" style="left:160px;top:1799px">
    <svg viewBox="0 0 68 68"><circle cx="34" cy="22" r="11"/><path d="M14 62 Q14 40 34 40 Q54 40 54 62 Z"/><path d="M20 22 Q20 8 34 8 Q48 8 48 22"/></svg>
    <h3>Transaction<br>Support</h3>
    <p>Acquisition, divestment and investment valuations to help you maximize your investment returns.</p>
  </div>
  <div class="abs service active" style="left:464px;top:1801px">
    <svg viewBox="0 0 68 68"><rect x="6" y="10" width="56" height="38"/><path d="M34 48 V58 M22 60 H46"/><path d="M20 40 V30 M28 40 V22 M36 40 V26 M44 40 V18"/></svg>
    <h3>Financial<br>Reporting</h3>
    <p>Purchase price allocations (PPA), goodwill analyses, impairment testing, intangible asset valuations</p>
  </div>
  <div class="abs service" style="left:766px;top:1801px">
    <svg viewBox="0 0 68 68"><rect x="18" y="4" width="40" height="56"/><path d="M26 14 H50 M26 22 H50 M26 30 H50 M26 38 H44"/><circle cx="16" cy="50" r="9"/><path d="M12 54 V50 M16 54 V46 M20 54 V48"/></svg>
    <h3>Fiscal<br>Valuations</h3>
    <p>Business valuations to support Dutch participation exemption, capital gains and significant interest tests</p>
  </div>
  <div class="abs service" style="left:157px;top:2128px">
    <svg viewBox="0 0 68 68"><rect x="26" y="6" width="36" height="26"/><path d="M30 26 L38 18 L46 22 L56 12"/><path d="M44 32 L40 44 M44 32 L48 44"/><path d="M6 62 H62"/><rect x="10" y="40" width="12" height="22"/></svg>
    <h3>Finance<br>Training</h3>
    <p>Open-enrollment training to the professional finance and banking markets Legal Support</p>
  </div>
  <div class="abs service" style="left:460px;top:2128px">
    <svg viewBox="0 0 68 68"><path d="M16 6 H46 L54 14 V62 H16 Z"/><path d="M24 40 H46 M24 48 H46 M24 56 H40"/><circle cx="35" cy="22" r="8"/><path d="M31 22 L34 25 L39 19"/></svg>
    <h3 style="margin-top:22px">Legal Support</h3>
    <p>Business valuations relating to contribution in kind statements “inbrengverklaring” when a company is initially funded with equity</p>
  </div>
  <div class="abs service" style="left:763px;top:2128px">
    <svg viewBox="0 0 68 68"><path d="M26 36 Q18 28 20 18 Q24 6 34 6 Q44 6 48 18 Q50 28 42 36 V44 H26 Z"/><path d="M28 50 H40 M30 56 H38"/><path d="M34 14 V2 M8 20 H2 M66 20 H60"/></svg>
    <h3 style="margin-top:22px">Capital Advisory</h3>
    <p>Analysis and assessment of strategic options from a valuation and financial perspective</p>
  </div>
</section>

<section class="news">
  <div class="abs news-band" role="img" aria-label="Faded stock market chart backdrop"></div>
  <svg class="abs" style="left:0;top:2990px" width="1200" height="260" viewBox="0 2990 1200 260">
    <path d="M0 3107 L366 3229 L1200 3015 L1200 3250 L0 3250 Z" fill="#eaf1f7"/>
    <path d="M0 3107 L340 3220 Q366 3230 392 3222 L1200 3015" fill="none" stroke="#0355a3" stroke-width="4"/>
  </svg>
  <div class="abs sec-head" style="top:2555px;color:#fff"><div class="mark">KR Appraisals</div><h2>Latest News</h2></div>

  <article class="abs news-card" style="left:158px;top:2665px">
    <div class="thumb" role="img" aria-label="Hands reviewing financial charts on a desk" style="background:linear-gradient(135deg,#eaf1f7,#85acd3 60%,#3277b5)"></div>
    <div class="body">
      <h3>Daniel Rourke to Speak at Route2Markets on Feb 18 in Lindenhoven</h3>
      <div class="date"><svg width="12" height="12" viewBox="0 0 12 12"><rect x="1" y="2" width="10" height="9" fill="none"/><path d="M1 5 H11"/></svg>Feb 3, 2019 at 9:42 am</div>
      <p>Sed ut perspiciatis unde omnis iste natus error sit voluptatem accuntium dolor-emque laudantium, totam</p>
    </div>
  </article>
  <article class="abs news-card" style="left:458px;top:2665px">
    <div class="thumb" role="img" aria-label="Advisors working with a tablet and documents" style="background:linear-gradient(135deg,#dfe8f1,#a9c2dc 55%,#5f86ad)"></div>
    <div class="body">
      <h3>KR Appraisals presenteert bij Route2Markets op 18 februari</h3>
      <div class="date"><svg width="12" height="12" viewBox="0 0 12 12"><rect x="1" y="2" width="10" height="9" fill="none"/><path d="M1 5 H11"/></svg>Feb 3, 2019 at 9:42 am</div>
      <p>Sed ut perspiciatis unde omnis iste natus error sit voluptatem accuntium dolor-emque laudantium, totam</p>
    </div>
  </article>
  <article class="abs news-card" style="left:760px;top:2665px">
    <div class="thumb" role="img" aria-label="Blue stock market data display" style="background:linear-gradient(135deg,#85acd3,#3277b5 45%,#0355a3)"></div>
    <div class="body">
      <h3>Hartley-Venn Enters into Strategic Partnership</h3>
      <div class="date"><svg width="12" height="12" viewBox="0 0 12 12"><rect x="1" y="2" width="10" height="9" fill="none"/><path d="M1 5 H11"/></svg>Feb 3, 2019 at 9:42 am</div>
      <p>Sed ut perspiciatis unde omnis iste natus error sit voluptatem accuntium dolor-emque laudantium, totam</p>
    </div>
  </article>
</section>

<section class="contact">
  <div class="abs contact-bg"></div>
  <div class="abs sec-head" style="top:3246px;color:var(--ink)"><div class="mark" style="color:var(--blue-deep)">KR Appraisals</div><h2>Contact Form</h2></div>
  <div class="abs field" style="left:142px;top:3358px;width:447px;height:50px">Name</div>
  <div class="abs field" style="left:142px;top:3427px;width:447px;height:50px">Email</div>
  <div class="abs field" style="left:142px;top:3495px;width:447px;height:50px">Phone</div>
  <div class="abs field area" style="left:608px;top:3358px;width:446px;height:187px">Message</div>
  <div class="abs captcha"><span class="box"></span>I'm not a robot</div>
  <div class="abs submit">Submit</div>
</section>

<footer>
  <div class="abs footer-brand">KR Appraisals</div>
  <nav class="abs footer-nav"><span>Home</span><span>Services</span><span>News &amp; Views</span><span>About</span><span>Career</span><span>Contact Us</span></nav>
  <div class="abs copy">© 2019 Company Name&nbsp; All right reserved</div>
  <div class="abs socials"><span></span><span></span><span></span><span></span></div>
</footer>

</body>
</html>
```